Tech business card design

We need an amazing business card design for our new business 'Pexla' a marketing tech startup based in Sydney, Australia. We provide an online marketplace for businesses to search and buy advertising media, connect with service providers and learn more about marketing. We wish to communicate 'cool tech', reliability and professionalism and design based around our logo.

Target Market(s)

Business Owners

Contact Information for Business Card

Name
Position
Email Address
Website
Phone Number

Font styles to use
Other font styles liked:
• Avenir & Avenir Next

Colors

Designer to choose colors to be used in the design.

```html
<!DOCTYPE html>
<html lang="en">
<head>
<meta charset="utf-8">
<title>Pexla Business Card</title>
<link rel="stylesheet" href="https://fonts.googleapis.com/css2?family=Nunito+Sans:wght@400;700;800;900&display=swap">
<style>
  :root {
    --backdrop: #1b1b1d;
    --navy: #141b45;
    --paper: #ffffff;
    --divider: #8a8d99;
    --ink-light: #ffffff;
    --ink-muted: #dfe2ee;
    --mark-faint: #5d648f;
  }
  * { box-sizing: border-box; margin: 0; padding: 0; }
  html, body {
    width: 1200px; height: 803px; overflow: hidden;
    background: var(--backdrop);
    font-family: "Nunito Sans", "Avenir Next", Arial, sans-serif;
  }
  .stage {
    width: 1200px; height: 803px;
    display: flex; align-items: center; justify-content: center; gap: 48px;
  }
  .card {
    position: relative;
    width: 525px; height: 300px;
    overflow: hidden;
    box-shadow: 0 18px 40px rgba(0,0,0,.55);
  }
  .card--front { background: var(--navy); }
  .card--back {
    background: var(--navy);
    display: flex; align-items: center; justify-content: center;
  }
  .front-split { position: absolute; inset: 0; }
  .brand {
    position: absolute; left: 26px; top: 118px;
    font-size: 74px; font-weight: 900; letter-spacing: -1px; line-height: 1;
    color: var(--navy);
  }
  .contact {
    position: absolute; left: 292px; top: 34px;
    color: var(--ink-light);
  }
  .contact__name { font-size: 17px; font-weight: 800; letter-spacing: .3px; }
  .contact__role { font-size: 11px; font-weight: 700; margin: 2px 0 16px 6px; }
  .contact__address { font-size: 12px; line-height: 1.35; color: var(--ink-muted); margin-bottom: 18px; }
  .contact__list { list-style: none; font-size: 13px; }
  .contact__list li { display: flex; align-items: center; gap: 10px; margin-bottom: 9px; }
  .contact__list svg { width: 12px; height: 12px; fill: var(--ink-light); flex: none; }
  .back-brand {
    font-size: 150px; font-weight: 900; letter-spacing: -3px; line-height: 1;
    color: var(--mark-faint);
  }
</style>
</head>
<body>
<main class="stage">
  <section class="card card--front" aria-label="Business card front">
    <svg class="front-split" viewBox="0 0 525 300" width="525" height="300" aria-hidden="true">
      <polygon points="0,0 240,0 240,44 250,52 240,60 262,300 0,300" fill="var(--paper)"/>
      <polyline points="240,0 240,44 250,52 240,60 262,300" fill="none" stroke="var(--divider)" stroke-width="4"/>
    </svg>
    <div class="brand">pexla</div>
    <div class="contact">
      <p class="contact__name">JANE DOE</p>
      <p class="contact__role">Position</p>
      <p class="contact__address">Street Name, City Name<br>Zipcode:012345</p>
      <ul class="contact__list">
        <li><svg viewBox="0 0 24 24"><path d="M6.6 10.8a15 15 0 0 0 6.6 6.6l2.2-2.2a1 1 0 0 1 1-.25 11.4 11.4 0 0 0 3.6.57 1 1 0 0 1 1 1V20a1 1 0 0 1-1 1A17 17 0 0 1 3 4a1 1 0 0 1 1-1h3.5a1 1 0 0 1 1 1c0 1.25.2 2.45.57 3.57a1 1 0 0 1-.25 1z"/></svg>012-345-6789</li>
        <li><svg viewBox="0 0 24 24"><path d="M2 5h20v14H2z M3 6l9 7 9-7" fill="none" stroke="#fff" stroke-width="2"/></svg>info@pexla.com</li>
        <li><svg viewBox="0 0 24 24"><circle cx="12" cy="12" r="9.5" fill="none" stroke="#fff" stroke-width="2"/><path d="M2.5 12h19M12 2.5c3 3 3 16 0 19M12 2.5c-3 3-3 16 0 19" fill="none" stroke="#fff" stroke-width="1.6"/></svg>www.pexla.com</li>
      </ul>
    </div>
  </section>
  <section class="card card--back" aria-label="Business card back">
    <div class="back-brand">pexla</div>
  </section>
</main>
</body>
</html>
```